Harbor Crestline (Business Card Design)

Need business cards designed. Something modern, chic, and sleek. Mabye the back of the card should be the navy blue that is in the logo and then just the logo on the back.

Target Market(s)

Those in the hotel, office, and renovation industry

Contact Information for Business Card

1. Logo 2. Dorian Fenwick 3. CEO/Founder 4. Phone: (833) HarbCre / (833) 427-2731 5. Email: dorian@theharborcrestline.com 6. Website: www.theharborcrestline.com

Font styles to use
Other font styles liked:
• Look at the logo font and base the font for everything else off of that.

Colors
0054AA
0677BA
7BADD7
CADEEF
E8F1F8

Requirements
Must have
• Colors that are associated in the logo
Nice to have
• Sleek modern clean and chic design.

```html
<!DOCTYPE html>
<html lang="en">
<head>
<meta charset="utf-8">
<title>Harbor Crestline — Business Card</title>
<link rel="stylesheet" href="https://fonts.googleapis.com/css2?family=Montserrat:wght@400;500;600;700&display=swap">
<style>
  :root {
    --navy: #0d1a45;
    --gold: #c9a13f;
    --white: #ffffff;
    --backdrop: #2b2b2b;
  }
  * { box-sizing: border-box; margin: 0; padding: 0; }
  html, body {
    width: 1200px; height: 1015px; overflow: hidden;
    background: var(--backdrop);
    font-family: "Montserrat", sans-serif;
  }
  .sheet {
    width: 1200px; height: 1015px;
    display: flex; flex-direction: column; align-items: center; justify-content: center;
    gap: 56px;
  }
  .card {
    position: relative;
    width: 760px; height: 434px;
    overflow: hidden;
  }
  .card--back { background: var(--navy); }
  .card--front { background: var(--white); }

  .wordmark {
    position: absolute;
    display: flex; align-items: center; gap: 16px;
    font-weight: 700;
    letter-spacing: 0.14em;
    text-transform: uppercase;
    line-height: 1.15;
  }
  .wordmark__mark {
    width: 18px; height: 18px; background: var(--gold); flex: none;
  }
  .card--back .wordmark {
    color: var(--white);
    font-size: 40px;
    left: 50%; top: 46%;
    transform: translate(-50%, -50%);
    white-space: nowrap;
  }
  .card--front .wordmark {
    color: var(--navy);
    font-size: 28px;
    right: 52px; top: 70px;
    white-space: nowrap;
  }

  .band {
    position: absolute;
    left: 0; bottom: 22px;
    width: 708px; height: 16px;
  }
  .band__cap {
    position: absolute;
    right: 22px; bottom: 30px;
    width: 22px; height: 18px;
    background: var(--gold);
  }
  .card--back .band { background: var(--white); }
  .card--front .band { background: var(--navy); }

  .person {
    position: absolute;
    left: 56px; top: 200px;
  }
  .person__name {
    color: var(--navy);
    font-weight: 700;
    font-size: 30px;
    letter-spacing: 0.01em;
  }
  .person__role {
    color: var(--gold);
    font-weight: 400;
    font-size: 18px;
    margin-top: 2px;
  }
  .contacts {
    list-style: none;
    margin-top: 26px;
  }
  .contacts__item {
    display: flex; align-items: center; gap: 12px;
    color: var(--navy);
    font-size: 19px;
    font-weight: 500;
    line-height: 1.5;
  }
  .contacts__icon { width: 18px; height: 18px; flex: none; }
</style>
</head>
<body>
<main class="sheet">
  <section class="card card--back" aria-label="Card back">
    <div class="wordmark"><span>Harbor Crestline</span><span class="wordmark__mark"></span></div>
    <div class="band"></div>
    <div class="band__cap"></div>
  </section>

  <section class="card card--front" aria-label="Card front">
    <div class="wordmark"><span>Harbor Crestline</span><span class="wordmark__mark"></span></div>

    <div class="person">
      <h1 class="person__name">DORIAN FENWICK</h1>
      <p class="person__role">CEO/FOUNDER</p>
      <ul class="contacts">
        <li class="contacts__item">
          <svg class="contacts__icon" viewBox="0 0 24 24" aria-hidden="true"><path fill="#0d1a45" d="M6.6 10.8a15.1 15.1 0 0 0 6.6 6.6l2.2-2.2a1 1 0 0 1 1-.25 11.4 11.4 0 0 0 3.6.57 1 1 0 0 1 1 1V20a1 1 0 0 1-1 1A17 17 0 0 1 3 4a1 1 0 0 1 1-1h3.5a1 1 0 0 1 1 1c0 1.25.2 2.45.57 3.57a1 1 0 0 1-.25 1z"/></svg>
          <span>(833) HarbCre / (833) 427-2731</span>
        </li>
        <li class="contacts__item">
          <svg class="contacts__icon" viewBox="0 0 24 24" aria-hidden="true"><path fill="#0d1a45" d="M2 5h20v14H2z"/><path fill="none" stroke="#fff" stroke-width="1.6" d="M2.5 5.5 12 13l9.5-7.5"/></svg>
          <span>dorian@theharborcrestline.com</span>
        </li>
        <li class="contacts__item">
          <svg class="contacts__icon" viewBox="0 0 24 24" aria-hidden="true"><g fill="none" stroke="#0d1a45" stroke-width="1.8"><circle cx="12" cy="12" r="9.5"/><ellipse cx="12" cy="12" rx="4" ry="9.5"/><path d="M2.5 12h19M4 7h16M4 17h16"/></g></svg>
          <span>www.theharborcrestline.com</span>
        </li>
      </ul>
    </div>

    <div class="band"></div>
    <div class="band__cap"></div>
  </section>
</main>
</body>
</html>
```